4D Cradle Glimpse Luxury Ultrasound Billboard

Design a HIGH-END, MODERN billboard for my private prenatal ultrasound studio, 4D Cradle Glimpse, located in Pace, Florida.
This billboard will be viewed by drivers traveling at highway speeds, so it must be extremely clean, simple, and readable within 6 seconds.
About My Business
4D Cradle Glimpse is a private prenatal ultrasound studio specializing in:
Highest technology 4D/HD Ultrasounds
Early Gender Determination
Pregnancy Confirmation
I have been serving families for nearly 10 years and is known for creating a memorable experience, not just an ultrasound appointment.
Design Style
I DO NOT want:
Flowers
Leaves
Swirls
Glitter
Hearts everywhere
Busy backgrounds
Generic maternity stock graphics
I DO want:
Modern
Luxury
Upscale
Clean
Professional
Eye-catching
Premium medical spa feel
Colors
Use colors from my logo:
LOGO Green ( or a deep green)
Black
White
Soft Gold accents
Images:
Incorporate my professional headshot in a clean, modern way, logo, and the ultrasound images
Text
Keep wording minimal.
Primary Headline ( OPEN TO IDEAS) :
EXAMPLES ( WOULD RATHER SOMETHING MORE CATCHY)
" ADVANCED IMAGING. UNFORGETTABLE MOMENTS"
"MEET YOUR BABY BEFORE BIRTH"
Under headline:
4D Ultrasound • Early Gender • Pregnancy Confirmation
Business Name:
4D Cradle Glimpse
Private Prenatal Ultrasound Studio
Phone Number:
850-471-5923
Important
This billboard must be readable in 5–6 seconds from a moving vehicle.
Less text is better.
The phone number and business name must be visible from a distance.
The design should feel like a premium brand that immediately tells expecting parents:
“This is where I go to see my baby.”
Files Provided
Official logo
Headshot
Ultrasound images
Don’t make this look like a medical office billboard.
Make it look like a luxury baby experience billboard. That’s what separates 4D Cradle Glimpse from hospitals, OB offices, and all the new studios popping up around you. The emotional connection is what gets moms to book. ❤️
Billboard Size - 10.6” x 36”

```html
<!DOCTYPE html>
<html lang="en">
<head>
<meta charset="utf-8">
<title>4D Cradle Glimpse Billboard</title>
<link href="https://fonts.googleapis.com/css2?family=Cinzel:wght@700;800&family=Damion&family=Roboto:wght@400&family=Roboto+Condensed:wght@400&display=swap" rel="stylesheet">
<style>
  :root {
    --stage: #6d6d6d;
    --deep-green: #15211c;
    --shade-green: #111a16;
    --gold: #c49a32;
    --gold-light: #e2bf5c;
    --gold-dark: #8f6b1c;
    --white: #ffffff;
  }
  * { margin: 0; padding: 0; box-sizing: border-box; }
  html, body { width: 1200px; height: 379px; overflow: hidden; background: var(--stage); }
  .billboard {
    position: absolute; left: 48px; top: 32px;
    width: 1104px; height: 315px;
    background: var(--deep-green);
    overflow: hidden;
    box-shadow: 0 2px 8px rgba(0,0,0,.35);
  }
  .billboard-art { position: absolute; inset: 0; }
  .gold-text {
    background: linear-gradient(180deg, var(--gold-light) 0%, var(--gold) 50%, var(--gold-dark) 100%);
    -webkit-background-clip: text; background-clip: text; color: transparent;
  }
  .headline-block { position: absolute; left: 400px; width: 400px; text-align: center; }
  .eyebrow {
    top: 31px; font-family: "Roboto", sans-serif; font-size: 24px;
    letter-spacing: 4px; color: var(--white); line-height: 1;
  }
  .headline {
    top: 64px; font-family: "Cinzel", serif; font-weight: 800;
    font-size: 32px; line-height: 31px;
  }
  .tagline {
    top: 134px; font-family: "Damion", cursive; font-size: 30px;
    color: var(--white); line-height: 1;
  }
  .services {
    position: absolute; left: 388px; width: 421px; top: 184px;
    display: flex; justify-content: space-between;
    font-family: "Roboto Condensed", sans-serif; font-size: 16px;
    color: var(--white); line-height: 1;
  }
  .brand-badge {
    position: absolute; left: 381px; top: 239px; width: 115px; height: 57px;
    background: var(--white); border-radius: 6px;
    border: 1.5px solid var(--gold);
    display: flex; align-items: center; justify-content: center;
  }
  .brand-name {
    font-family: "Cinzel", serif; font-weight: 700; font-size: 12.5px;
    color: var(--deep-green); text-align: center; line-height: 1.15;
  }
  .phone-label {
    position: absolute; left: 603px; top: 239px;
    font-family: "Roboto Condensed", sans-serif; font-size: 19px;
    color: var(--white); line-height: 1;
  }
  .phone-number {
    position: absolute; left: 603px; top: 260px;
    font-family: "Cinzel", serif; font-weight: 700; font-size: 35px;
    line-height: 1; white-space: nowrap;
  }
</style>
</head>
<body>
<div class="billboard">
  <svg class="billboard-art" viewBox="0 0 1104 315" width="1104" height="315">
    <defs>
      <linearGradient id="goldGrad" x1="0" y1="0" x2="0" y2="1">
        <stop offset="0" stop-color="#e2bf5c"/>
        <stop offset="1" stop-color="#a77d22"/>
      </linearGradient>
      <radialGradient id="headshotGrad" cx="0.5" cy="0.4" r="0.6">
        <stop offset="0" stop-color="#c9a27c"/>
        <stop offset="0.55" stop-color="#a98861"/>
        <stop offset="1" stop-color="#3d5240"/>
      </radialGradient>
      <radialGradient id="scanGrad" cx="0.45" cy="0.45" r="0.6">
        <stop offset="0" stop-color="#a65544"/>
        <stop offset="0.6" stop-color="#80362b"/>
        <stop offset="1" stop-color="#3a1410"/>
      </radialGradient>
    </defs>
    <circle class="backdrop-arc" cx="160" cy="10" r="300" fill="#111a16"/>
    <path class="gold-swoop" d="M290 215 A230 230 0 0 1 360 315 L330 315 A210 210 0 0 0 290 235 Z" fill="url(#goldGrad)"/>
    <path class="headshot" role="img" aria-label="Professional headshot of the studio owner"
          d="M16 315 L20 210 C30 150 70 120 90 90 C105 30 160 5 200 15 C250 30 270 90 280 160 C300 200 300 260 298 315 Z"
          fill="url(#headshotGrad)"/>
    <circle class="gold-crescent" cx="1050" cy="155" r="240" fill="url(#goldGrad)"/>
    <circle class="crescent-gap" cx="1010" cy="158" r="192" fill="#15211c"/>
    <circle class="ultrasound-scan" role="img" aria-label="4D ultrasound image of twin babies face to face"
            cx="1004" cy="155" r="182" fill="url(#scanGrad)"/>
    <path class="tagline-underline" d="M521 171 Q600 167 677 171 Q600 174 521 171 Z" fill="url(#goldGrad)" stroke="#c49a32" stroke-width="1.2"/>
    <line class="divider" x1="388" y1="221" x2="809" y2="221" stroke="#3a4741" stroke-width="1"/>
    <circle class="phone-ring" cx="567" cy="267" r="24.5" fill="none" stroke="#c49a32" stroke-width="2"/>
    <path class="phone-icon" fill="#ffffff"
          d="M560.5 258.5 c1-1 2.3-1 3 .2 l2 3.2 c.5 .9 .3 2-.5 2.6 l-1.3 1 c1 2.2 2.7 4 4.9 5 l1-1.3 c.6-.8 1.7-1 2.6-.5 l3.2 2 c1.2 .7 1.2 2 .2 3 l-1.3 1.3 c-1.6 1.6-4.2 1.6-7.6-.6 -3.6-2.4-6.2-5.4-7.5-8.6 -1.2-3-.9-5.3 .4-6.6 Z"/>
  </svg>

  <div class="headline-block eyebrow">ADVANCED IMAGING</div>
  <div class="headline-block headline gold-text">UNFORGETTABLE<br>MOMENTS</div>
  <div class="headline-block tagline">Meet Your Baby Before Birth</div>

  <div class="services">
    <span>4D Ultrasound</span><span>•</span><span>Early Gender</span><span>•</span><span>Pregnancy Confirmation</span>
  </div>

  <div class="brand-badge"><span class="brand-name">4D Cradle<br>Glimpse</span></div>

  <div class="phone-label">Phone Number</div>
  <div class="phone-number gold-text">850-471-5923</div>
</div>
</body>
</html>
```